Help our Sugar Loom find our winning design! We're looking for a business card....

We’re a Sugar Loom in NY specializing in custom-made cakes and unique desserts.
Our cakes combine flavor and art, each designed to match customer’s special event and theme.
We’d like a unique business card with a clean design that will combine French chic and artistic look & feel.
We’d like to differentiate ourselves from standard bakeries, please don’t offer cupcake images :-)
Our logo is peach-pink and brown and we’d love to use these colors ( . Another color that can be added is gold - or feel free to suggest!

Target Market(s)

Women, ages 25-55

Industry/Entity Type

Boutique

Contact Information for Business Card

Text on card:
Logo
Sugar Loom by Dana Welch

www.sugarloomsweets.com
hello@sugarloom.com
(516) 555-0147
F – sugarloomnyc
IG - sugarloom_ny

Font styles to use
Sans Serif
Script

Requirements
Must have
• Logo
• Clean look
• French chic and artistic look & feel.
Nice to have
• Damask pattern
Should not have
• Cupcake images

```html
<!DOCTYPE html>
<html lang="en">
<head>
<meta charset="utf-8">
<title>Sugar Loom – Business Card</title>
<link rel="stylesheet" href="https://fonts.googleapis.com/css2?family=Exo+2:wght@300;400;500&display=swap">
<style>
  :root {
    --backdrop: #ecebe9;
    --card-white: #ffffff;
    --card-grey: #676461;
    --silver-light: #f1f1f1;
    --silver-mid: #c9c9c9;
    --silver-dark: #9a9a9a;
    --ink: #3a3735;
    --ink-soft: #6d6966;
    --text-light: #ffffff;
    --brand: #b9727e;
  }
  * { margin: 0; padding: 0; box-sizing: border-box; }
  html, body { width: 1200px; height: 828px; overflow: hidden; }
  body {
    background: var(--backdrop);
    font-family: "Exo 2", Arial, sans-serif;
  }
  .canvas { position: relative; width: 1200px; height: 828px; }

  .card {
    position: absolute;
    width: 540px;
    height: 309px;
    overflow: hidden;
    box-shadow: 0 6px 18px rgba(0,0,0,.14);
  }
  .card-front { left: 40px; top: 260px; background: var(--card-white); }
  .card-back  { left: 620px; top: 260px; background: var(--card-grey); }
  .card-art { position: absolute; inset: 0; width: 100%; height: 100%; }

  .brand {
    position: absolute;
    display: flex;
    flex-direction: column;
    align-items: center;
    gap: 6px;
  }
  .brand-name {
    font-size: 26px;
    font-weight: 400;
    color: var(--brand);
    letter-spacing: 1px;
    display: flex;
    align-items: center;
    gap: 8px;
  }
  .brand-dot {
    width: 10px; height: 10px; border-radius: 50%;
    background: var(--brand);
  }
  .brand-tagline {
    font-size: 8px;
    letter-spacing: 2px;
    color: var(--ink-soft);
    text-transform: uppercase;
  }
  .card-front .brand { left: 150px; top: 78px; width: 240px; }
  .card-back .brand { left: 20px; top: 170px; width: 200px; }

  .front-web {
    position: absolute;
    left: 0; right: 0; bottom: 34px;
    text-align: center;
    font-size: 17px;
    letter-spacing: 5px;
    color: var(--ink);
  }

  .owner {
    position: absolute;
    right: 28px; top: 26px;
    text-align: right;
    color: var(--text-light);
  }
  .owner-name { font-size: 18px; font-weight: 400; letter-spacing: 1.5px; text-transform: uppercase; }
  .owner-title { font-size: 11px; font-weight: 300; letter-spacing: .5px; margin-top: 2px; }

  .address {
    position: absolute;
    right: 28px; top: 94px;
    text-align: right;
    font-size: 11px;
    line-height: 15px;
    color: var(--text-light);
    letter-spacing: .4px;
  }
  .contact-list {
    position: absolute;
    right: 28px; top: 148px;
    list-style: none;
    text-align: right;
    color: var(--text-light);
    font-size: 11px;
    letter-spacing: .4px;
  }
  .contact-list li {
    display: flex;
    justify-content: flex-end;
    align-items: center;
    gap: 7px;
    height: 19px;
  }
  .contact-list svg { width: 11px; height: 11px; fill: var(--text-light); stroke: var(--text-light); }
</style>
</head>
<body>
<main class="canvas">

  <section class="card card-front" aria-label="Card front">
    <svg class="card-art" viewBox="0 0 540 309" aria-hidden="true">
      <defs>
        <linearGradient id="front-fill" x1="0" y1="0" x2="0" y2="1">
          <stop offset="0" stop-color="#ffffff"/>
          <stop offset="1" stop-color="#dcdcdc"/>
        </linearGradient>
        <linearGradient id="front-edge" x1="0" y1="0" x2="1" y2="0">
          <stop offset="0" stop-color="#e6e6e6"/>
          <stop offset=".5" stop-color="#a8a8a8"/>
          <stop offset="1" stop-color="#dedede"/>
        </linearGradient>
      </defs>
      <path d="M0,215 C170,205 380,150 540,30 L540,309 L0,309 Z" fill="url(#front-fill)"/>
      <path d="M0,215 C170,205 380,150 540,30" fill="none" stroke="url(#front-edge)" stroke-width="7"/>
    </svg>
    <div class="brand">
      <span class="brand-name"><span class="brand-dot"></span>Sugar Loom</span>
      <span class="brand-tagline">Custom Cakes Boutique</span>
    </div>
    <p class="front-web">www.sugarloomsweets.com</p>
  </section>

  <section class="card card-back" aria-label="Card back">
    <svg class="card-art" viewBox="0 0 540 309" aria-hidden="true">
      <defs>
        <linearGradient id="back-edge" x1="0" y1="0" x2="0" y2="1">
          <stop offset="0" stop-color="#f4f4f4"/>
          <stop offset=".5" stop-color="#9d9d9d"/>
          <stop offset="1" stop-color="#e8e8e8"/>
        </linearGradient>
      </defs>
      <path d="M0,0 L180,0 C255,60 275,210 250,309 L0,309 Z" fill="#ffffff"/>
      <path d="M180,0 C255,60 275,210 250,309" fill="none" stroke="url(#back-edge)" stroke-width="7"/>
    </svg>

    <div class="brand">
      <span class="brand-name"><span class="brand-dot"></span>Sugar Loom</span>
      <span class="brand-tagline">Custom Cakes Boutique</span>
    </div>

    <div class="owner">
      <p class="owner-name">Dana Welch</p>
      <p class="owner-title">Managing Director</p>
    </div>

    <p class="address">214 Mott Street, Floor 3<br>New York NY</p>

    <ul class="contact-list">
      <li>(516) 555-0147
        <svg viewBox="0 0 12 12"><path d="M2.5 1l2 2.2-1 1.3c.7 1.5 1.8 2.6 3.3 3.3l1.3-1 2.2 2-1 1.7C5.5 10.4 1.6 6.5 1 2z" stroke="none"/></svg>
      </li>
      <li>(516) 555-0148
        <svg viewBox="0 0 12 12"><rect x="3" y=".8" width="6" height="10.4" rx="1" fill="none" stroke-width="1.1"/><circle cx="6" cy="9.6" r=".6" stroke="none"/></svg>
      </li>
      <li>(516) 555-0149
        <svg viewBox="0 0 12 12"><rect x="3" y="1" width="6" height="3" stroke="none"/><rect x="1" y="4.5" width="10" height="5" rx="1" stroke="none"/><rect x="3" y="8" width="6" height="3" fill="#676461" stroke-width=".8"/></svg>
      </li>
      <li>hello@sugarloom.com
        <svg viewBox="0 0 12 12"><rect x=".8" y="2.2" width="10.4" height="7.6" rx=".8" fill="none" stroke-width="1"/><path d="M1 2.6l5 4 5-4" fill="none" stroke-width="1"/></svg>
      </li>
      <li>www.sugarloomsweets.com
        <svg viewBox="0 0 12 12"><circle cx="6" cy="6" r="5" fill="none" stroke-width="1"/><ellipse cx="6" cy="6" rx="2.2" ry="5" fill="none" stroke-width=".9"/><path d="M1 6h10" stroke-width=".9"/></svg>
      </li>
    </ul>
  </section>

</main>
</body>
</html>
```